Brand new redesign of Brightpath finance website

I need a new website design that i can advertise a great low interest rate on the front page and capture input application details that will send through to my email address.

some car finance companies will be similar to this would be listed below

tallowcredit.example.com.au
mirabelfinance.example.com.au
finance725.example.com.au
quenbyfinance.example.com.au
finance91.example.com.au

Reason: I have changed the project to a committed project. all the webpages should have the same format just different content and i want to be able to edit the front page easily to update my interest rates.

Target Market(s)

Australian Finance market targeting a younger demographic

Industry/Entity Type

Finance

Coding

Coded - Design and coding required

Number of Pages Required

5+ page

Font styles to use
Serif
Sans Serif

Colors
0255a3
ffffff
cedeed

Requirements
Must have
• application capture form
• apply now buttons
• Headline rate front page

```html
<!DOCTYPE html>
<html lang="en">
<head>
<meta charset="utf-8">
<title>Brightpath Finance</title>
<link href="https://fonts.googleapis.com/css2?family=Lato:wght@400;700&family=Ubuntu:wght@500;700&display=swap" rel="stylesheet">
<style>
:root{
  --blue:#0255a3;
  --blue-dark:#01427f;
  --white:#ffffff;
  --pale:#cedeed;
  --ink:#231f20;
  --text:#333333;
  --field:#eeeeee;
  --field-line:#dddddd;
}
*{margin:0;padding:0;box-sizing:border-box}
html,body{width:813px;height:1200px;overflow:hidden;background:var(--white)}
body{position:relative;font-family:'Lato',sans-serif;color:var(--text)}
.abs{position:absolute}
.head-font{font-family:'Ubuntu',sans-serif}

/* top bar and header */
.top-bar{left:0;top:0;width:813px;height:22px;background:var(--blue)}
.apply-tab{left:640px;top:0;width:84px;height:22px;background:#e9eef4;color:var(--blue);font-size:8.5px;display:flex;align-items:center;justify-content:center;gap:6px}
.header{left:0;top:22px;width:813px;height:80px;background:var(--ink)}
.brand{left:88px;top:58px;display:flex;align-items:center;gap:6px;color:var(--white);font-family:'Ubuntu',sans-serif;font-weight:700;font-size:14px;letter-spacing:.5px}
.brand-dot{width:14px;height:14px;border-radius:50%;background:var(--blue)}
.phone{left:558px;top:42px;color:#e6e6e6;font-size:10px;display:flex;align-items:center;gap:6px}
.socials{display:flex;gap:7px}
.socials span{width:18px;height:18px;background:var(--blue);border-radius:2px;display:block}
.head-socials{left:656px;top:40px}
.nav{left:226px;top:72px;display:flex;align-items:center;font-family:'Ubuntu',sans-serif;font-weight:500;font-size:8.6px;color:var(--white)}
.nav a{color:var(--white);text-decoration:none;margin-right:20px;height:18px;display:flex;align-items:center}
.nav a.active{background:var(--blue);padding:0 8px;margin-right:11px}
.nav a:last-child{margin-right:0}

/* hero */
.hero{left:0;top:102px;width:813px;height:317px;background:linear-gradient(100deg,#b3121a 0%,#d63a1e 25%,#f29a35 45%,#fbd98a 58%,#c9a57a 75%,#8f7f6c 100%)}
.rate-badge{left:90px;width:228px;background:rgba(35,25,25,.82);border-radius:3px;color:var(--white);font-family:'Ubuntu',sans-serif;font-weight:500;font-size:12px;line-height:16px;padding:0 11px;display:flex;align-items:center}
.dots{left:386px;top:399px;display:flex;gap:6px}
.dots i{width:6px;height:6px;border-radius:50%;background:rgba(255,255,255,.8);display:block}
.dots i.on{background:transparent;border:1.5px solid var(--blue);box-shadow:0 0 0 1px #fff}

/* quote form */
.quote-form{left:514px;top:129px;width:210px;height:265px;background:var(--white);border-radius:3px;box-shadow:0 2px 6px rgba(0,0,0,.3)}
.quote-title{position:absolute;left:0;top:0;width:210px;height:30px;background:var(--blue);color:var(--white);font-family:'Ubuntu',sans-serif;font-weight:700;font-size:15px;padding-left:8px;display:flex;align-items:center;border-radius:3px 3px 0 0}
.field-label{position:absolute;left:8px;font-size:7.5px;color:#555}
.field{position:absolute;left:8px;width:194px;height:21px;background:var(--field);border:1px solid var(--field-line);font-size:8px;color:#444;padding-left:5px;display:flex;align-items:center}
.field svg{position:absolute;right:8px;top:7px}
.submit{position:absolute;left:8px;top:231px;width:70px;height:22px;background:#555b61;border-radius:2px;color:var(--white);font-family:'Ubuntu',sans-serif;font-weight:700;font-size:10.5px;display:flex;align-items:center;justify-content:center}

/* pre approval */
.section-title{color:var(--blue);font-family:'Ubuntu',sans-serif;font-weight:500;font-size:19px;letter-spacing:.4px}
.pre-title{left:90px;top:443px}
.rule{height:1px;background:linear-gradient(90deg,var(--pale),#a9c3dd,var(--pale))}
.pre-rule{left:90px;top:470px;width:306px}
.pre-copy{left:90px;top:484px;width:310px;font-size:8.4px;line-height:14.1px;color:#333}
.pre-bold{left:90px;top:576px;width:310px;font-size:8.4px;line-height:14.1px;font-weight:700;color:#222}
.pre-call{left:90px;top:612px;font-size:11.5px;color:#333;display:flex;align-items:baseline;gap:5px}
.pre-call b{color:var(--blue);font-size:13px}

.tile{width:141px;background:var(--blue);color:var(--white);font-family:'Ubuntu',sans-serif;font-weight:500;font-size:10.8px;letter-spacing:.3px;display:flex;flex-direction:column;align-items:center}
.tile .icon{width:41px;height:41px;border-radius:50%;background:var(--white);display:flex;align-items:center;justify-content:center;margin-top:13px;margin-bottom:10px}
.tile-hub{left:554px;top:519px;width:38px;height:38px;border-radius:50%;background:var(--white);border:3px solid var(--blue)}

/* promos */
.promo{top:656px;width:407px;height:202px;color:var(--white);text-align:center}
.promo-left{left:0;background:linear-gradient(135deg,#1f6bb3,#3f86c4 50%,#2b71b4)}
.promo-right{left:406px;background:linear-gradient(135deg,#3a3f46,#6b6e72 45%,#2c2f33)}
.promo h2{font-family:'Ubuntu',sans-serif;font-weight:500;font-size:16.5px;line-height:23px;letter-spacing:.4px}
.promo p{font-size:11.5px;line-height:17px;margin-top:7px}
.pill{display:inline-flex;align-items:center;gap:9px;height:23px;border-radius:12px;background:#e3edf7;color:var(--blue);font-family:'Ubuntu',sans-serif;font-weight:500;font-size:10.5px;padding:0 14px 0 4px;margin-top:12px}
.pill i{width:17px;height:17px;border-radius:50%;background:#9fb3c8;display:block}

/* solutions */
.sol-title{left:0;top:881px;width:813px;text-align:center}
.sol-rule{left:254px;top:913px;width:305px}
.sol-mark{left:214px;top:938px;width:96px;height:88px;border-radius:50%;border:5px solid var(--blue)}
.sol-lines{left:300px;top:940px}
.sol-item{left:370px;font-family:'Ubuntu',sans-serif;font-weight:500;font-size:11px;letter-spacing:.4px;color:#222;display:flex;align-items:center;gap:6px}
.sol-item i{width:3px;height:3px;border-radius:50%;background:#2a8bd0;display:block}

/* contact band */
.contact{left:0;top:1050px;width:813px;height:94px;background:var(--pale)}
.contact-item{top:1082px;display:flex;gap:9px;font-size:10px;color:#222;line-height:17px}
.contact-item b{font-family:'Ubuntu',sans-serif;font-weight:500;font-size:10px;display:block}
.c-icon{width:22px;height:22px;border-radius:50%;background:var(--blue);flex:none;display:flex;align-items:center;justify-content:center;margin-top:2px}
.divider{top:1072px;width:1px;height:52px;background:#b5c9dc}

/* footer */
.footer{left:0;top:1144px;width:813px;height:56px;background:var(--blue)}
.foot-nav{left:90px;top:1157px;display:flex;gap:11px;font-family:'Ubuntu',sans-serif;font-weight:500;font-size:7.8px;color:var(--white);letter-spacing:.4px}
.foot-copy{left:90px;top:1175px;font-family:'Ubuntu',sans-serif;font-weight:500;font-size:7.5px;color:var(--white);letter-spacing:.3px}
.foot-socials{left:656px;top:1163px}
.foot-socials span{background:#2f78bd}
</style>
</head>
<body>

<div class="abs top-bar"></div>
<div class="abs apply-tab">
  <svg width="10" height="11" viewBox="0 0 10 11"><path d="M1 .5h6l2 2v8H1z" fill="none" stroke="#333"/><path d="M3 5h4M3 7h4" stroke="#333"/></svg>
  Apply Now
</div>

<header class="abs header"></header>
<div class="abs brand"><span class="brand-dot"></span>BRIGHTPATH FINANCE</div>
<div class="abs phone">
  <svg width="14" height="14" viewBox="0 0 14 14"><path d="M3 1l2 3-1.3 1.3a7 7 0 0 0 5 5L10 9l3 2-1 2C6 13 1 8 1 2z" fill="none" stroke="#ddd" stroke-width="1"/></svg>
  1300 555 019
</div>
<div class="abs socials head-socials" aria-label="Social links"><span></span><span></span><span></span></div>
<nav class="abs nav">
  <a class="active">HOME</a><a>ABOUT</a><a>VEHICLE LOANS</a><a>OTHER LOANS</a><a>INSURANCE</a><a>FINANCE CALCULATOR</a><a>CONTACT</a>
</nav>

<section class="abs hero" role="img" aria-label="Photo of a red car speeding along a sunlit road with a best price guarantee stamp"></section>
<div class="abs rate-badge" style="top:256px;height:38px">LOW RATE CAR LOANS FROM 4.69%<br>COMPARISON RATE 4.99%</div>
<div class="abs rate-badge" style="top:307px;height:38px">LOW FEES</div>
<div class="abs rate-badge" style="top:358px;height:38px">LOW TOTAL COST LOANS</div>
<div class="abs dots"><i></i><i class="on"></i><i></i><i></i></div>

<form class="abs quote-form">
  <div class="quote-title">LET'S GET STARTED NOW!</div>
  <div class="field-label" style="top:44px">Loan Amount</div>
  <div class="field" style="top:60px"></div>
  <div class="field-label" style="top:89px">Deposit (If Any)</div>
  <div class="field" style="top:105px"></div>
  <div class="field-label" style="top:133px">Purpose of Loan</div>
  <div class="field" style="top:149px">Car<svg width="10" height="6" viewBox="0 0 10 6"><path d="M0 0h10L5 6z" fill="#444"/></svg></div>
  <div class="field-label" style="top:177px">Postal Code</div>
  <div class="field" style="top:193px"></div>
  <div class="submit">SUBMIT</div>
</form>

<h1 class="abs section-title pre-title">ONLINE LOAN PRE APPROVAL</h1>
<div class="abs rule pre-rule"></div>
<p class="abs pre-copy">Lorem ipsum dolor sit amet, consectetuer adipiscing elit, sed dia nonummy laoreet dolore magna aliquam erat volutpat. Ut wisi enim ad minim veniam, quis nostrud exerci tation ullamcorper suscipit lobortis nisl ut aliquip ex eaLorem ipsum dolor sit amet, consectetuer adipiscing elit, sed dia nonummy laoreet dolore magna aliquam erat volutpat. Ut wisi enim ad minim veniam, quis nostrud exerci tation ullamcorper suscipit lobortis</p>
<p class="abs pre-bold">Lorem ipsum dolor sit amet, consectetuer adipiscing elit, sed dia nonummy laoreet dolore magna aliquam erat volutpat.</p>
<p class="abs pre-call">Fill Out Our Quick Form Below or <b>Call 1300 555 019</b></p>

<div class="abs tile" style="left:429px;top:446px;height:87px">
  <div class="icon"><svg width="24" height="18" viewBox="0 0 24 18"><path d="M3 9l3-6h12l3 6v6h-3v-2H6v2H3z" fill="#0255a3"/><circle cx="7" cy="11" r="1.5" fill="#fff"/><circle cx="17" cy="11" r="1.5" fill="#fff"/></svg></div>
  VEHICLE LOANS
</div>
<div class="abs tile" style="left:582px;top:446px;height:87px">
  <div class="icon"><svg width="24" height="20" viewBox="0 0 24 20"><path d="M9 2h6v4h4v4H5V6h4z" fill="#0255a3"/><path d="M2 11h20l-3 7H5z" fill="#0255a3"/></svg></div>
  BOAT LOANS
</div>
<div class="abs tile" style="left:429px;top:544px;height:86px">
  <div class="icon"><svg width="22" height="20" viewBox="0 0 22 20"><path d="M11 1l10 9h-3v9h-5v-6H9v6H4v-9H1z" fill="#0255a3"/></svg></div>
  HOME LOANS
</div>
<div class="abs tile" style="left:582px;top:544px;height:86px">
  <div class="icon"><svg width="20" height="20" viewBox="0 0 20 20"><circle cx="10" cy="6" r="4" fill="#0255a3"/><path d="M2 19c0-5 3-7 8-7s8 2 8 7z" fill="#0255a3"/></svg></div>
  PERSONAL LOANS
</div>
<div class="abs tile-hub"></div>

<section class="abs promo promo-left" role="img" aria-label="Blue-toned photo of hands using a calculator">
  <div style="padding-top:31px">
    <h2>WHAT WILL<br>MY REPAYMENTS BE?</h2>
    <p>See How Much You Could Borrow With<br>Our Loan Calculator</p>
    <span class="pill"><i></i>LOAN CALCULATOR</span>
  </div>
</section>
<section class="abs promo promo-right" role="img" aria-label="Dark photo of a young driver leaning on a car">
  <div style="padding-top:39px">
    <h2>FIND OUT WHAT GUARANTEED<br>APPROVAL ACTUALLY MEANS</h2>
    <p>We Explain What it Means and<br>What We Offer Instead</p>
    <span class="pill"><i></i>FIND OUT MORE</span>
  </div>
</section>

<h2 class="abs section-title sol-title">BRIGHTPATH SOLUTIONS</h2>
<div class="abs rule sol-rule"></div>
<div class="abs sol-mark"></div>
<svg class="abs sol-lines" width="72" height="84" viewBox="0 0 72 84">
  <g stroke="#5aa5dc" stroke-width=".7" stroke-dasharray="1.5 1.5" fill="none">
    <path d="M8 38L70 6"/><path d="M8 40L70 30"/><path d="M8 42L70 55"/><path d="M8 44L70 81"/>
  </g>
</svg>
<div class="abs sol-item" style="top:939px"><i></i>BAS AGENT</div>
<div class="abs sol-item" style="top:963px"><i></i>PAYROLL AND BOOKKEEPING SERVICES</div>
<div class="abs sol-item" style="top:988px"><i></i>CREDIT FILE REPAIR / DEFAULT REMOVALS</div>
<div class="abs sol-item" style="top:1014px"><i></i>DEBT CONSOLIDATION</div>

<section class="abs contact"></section>
<div class="abs contact-item" style="left:89px">
  <span class="c-icon"><svg width="10" height="12" viewBox="0 0 10 12"><path d="M5 12C1 7 1 5 1 4a4 4 0 0 1 8 0c0 1 0 3-4 8z" fill="#fff"/><circle cx="5" cy="4" r="1.5" fill="#0255a3"/></svg></span>
  <div><b>BRIGHTPATH FINANCE</b>45 Harbour Lane, Sydney NSW 2000</div>
</div>
<div class="abs divider" style="left:354px"></div>
<div class="abs contact-item" style="left:393px">
  <span class="c-icon"><svg width="11" height="11" viewBox="0 0 14 14"><path d="M3 1l2 3-1.3 1.3a7 7 0 0 0 5 5L10 9l3 2-1 2C6 13 1 8 1 2z" fill="#fff"/></svg></span>
  <div><b>CALL US</b>1300 555 019</div>
</div>
<div class="abs divider" style="left:532px"></div>
<div class="abs contact-item" style="left:571px">
  <span class="c-icon"><svg width="11" height="8" viewBox="0 0 11 8"><rect x=".5" y=".5" width="10" height="7" fill="#fff"/><path d="M.5 .5l5 4 5-4" stroke="#0255a3" fill="none"/></svg></span>
  <div><b>EMAIL US</b>info@brightpathfinance.example.com</div>
</div>

<footer class="abs footer"></footer>
<div class="abs foot-nav"><span>HOME</span><span>ABOUT</span><span>VEHICLE LOANS</span><span>OTHER LOANS</span><span>INSURANCE</span><span>FINANCE CALCULATOR</span><span>CONTACT</span></div>
<div class="abs foot-copy">COPYRIGHT © 2016 BRIGHTPATH FINANCE. ALL RIGHTS RESERVED.</div>
<div class="abs socials foot-socials" aria-label="Social links"><span></span><span></span><span></span></div>

</body>
</html>
```